The Quiet Harvest Book Cover

Cover for Multiauthor Ebook & Paper Print Book Cover

Book Title:
The Quiet Harvest: Lessons of Insight From A Circle of Mentors to Guide You Toward a Fuller Journey

This book will offer the wisdom and philosophies of a variety of different coaches to allow future clients to get a taste of you and your style and prepare them to work with you!

A coach does not fix you. Or heal you. They coach you - offer thoughts to ponder, guidance, techniques to try. All to help you plays and succeed at the game of life.

Each coach has their own personality, training, experience, method and philosophy they bring to the table. The underlying purpose is to guide you through the quiet harvest, to become the person you desire and aspire to be. Different coaches for different folks, yet they all have their own unique wisdom and special sauce to share.

This book is a collection of just that. A tasting of the wisdom and philosophies of a variety of different coaches for you to experience.

Types of Coaches: Clarity, Dreams, Goals, Motivation, Mindset,  Subconscious, Beliefs, Behavior, Accountability, Life, Wellness, Love & Dating, Relationships, Sex, Business, Career,  Executive,  Personal Development,  Writing, Wellness, Fitness, Parenting,  Style, Spirituality, Public Speaking, Financial,  Time management, Weight Loss, Running, Self esteem,  Tarot, Astrology, Enneagram, Soul path/ Dharma, Skills, Performance,  Speaking / Communication, Leadership, Shadow Work, Acting, Sports, ANY & ALL

Target Market(s)

Males or females looking for guidance and words of wisdom from an expert coach - maybe to find one that resonates with them to work with further. Ages 16 and up. Any Gender. International. Looking to improve their life!

Industry/Entity Type

Self Development, Wellness, Coaching, Personal Growth, Fitness, Spirituality, Business, Relationships

Font styles to use
Serif
Script

Colors
0054AA
0677BA
7BADD7
CADEEF
E8F1F8
FFF300
FFF600
FEFA6F
FFFEC7
FFFEE8

Requirements
Must have
• I am looking for a visually appealing, unique cover that encompasses the breadth and depth of the transformation that people can go through and inspires them to want to grow and change even more. I love when elegant and classic simplicity is combined with some kind of twist that catches the eye and provokes thought. I love complimentary fonts, colors, design elements. You can visit my Brindlemart Author Page - Dr. Marisol Pendergast Voyle to see my titles to see what I have liked! But I am also excited to see where you can make my vision even better!!
Nice to have
• Front Cover - Image, Title and Subtitle, The Lantern Publishing House, Spine - Title and Publishing House Logo, Back - Book Blurb, Authors Names, Info about Publishing House, ISBN Barcode
Should not have
• Anything too feminine or too masculine as I want to encourage coaches of all genders to participate.

```html
<!DOCTYPE html>
<html lang="en">
<head>
<meta charset="utf-8">
<title>The Quiet Harvest — Book Cover Wrap</title>
<link rel="stylesheet" href="https://fonts.googleapis.com/css2?family=Allura&family=Cinzel:wght@600;700&family=Old+Standard+TT&family=Poppins:wght@400;500&display=swap">
<style>
  :root {
    --paper: #c1c1bf;
    --navy: #283253;
    --white: #ffffff;
    --wing-deep: #0b1640;
    --wing-mid: #143a78;
    --wing-light: #2fa8d8;
  }
  * { margin: 0; padding: 0; box-sizing: border-box; }
  html, body { width: 1200px; height: 831px; overflow: hidden; background: var(--paper); }
  .cover-wrap {
    position: relative;
    width: 1200px; height: 831px;
    background: var(--paper);
    font-family: "Poppins", sans-serif;
    overflow: hidden;
  }

  /* ---------- Back cover ---------- */
  .back-title {
    position: absolute; left: 0; width: 554px; top: 80px;
    text-align: center; color: #111;
    font-family: "Old Standard TT", serif;
  }
  .back-title h2 {
    font-weight: 400; font-size: 25px; letter-spacing: 1.2px; line-height: 1;
    transform: scaleY(1.05);
  }
  .back-title p {
    font-size: 9.4px; line-height: 10px; letter-spacing: 0.4px; margin-top: 4px;
  }
  .blurb {
    position: absolute; left: 97px; top: 157px; width: 359px;
    color: var(--white); font-size: 10.6px; line-height: 14.8px;
    text-align: justify;
  }
  .blurb p + p { margin-top: 14.6px; }
  .authors-heading {
    position: absolute; left: 0; width: 554px; top: 370px;
    text-align: center; color: var(--navy); font-size: 11px; font-weight: 500;
  }
  .author-list {
    position: absolute; top: 417px; list-style: none;
    color: var(--navy); font-size: 11px; line-height: 14.75px;
  }
  .author-list.col-a { left: 171px; }
  .author-list.col-b { left: 317px; }

  .publisher-band {
    position: absolute; left: 0; top: 613px; width: 646px; height: 218px;
    background: var(--navy);
  }
  .publisher-about {
    position: absolute; left: 95px; top: 633px; width: 363px;
    color: var(--white); font-size: 10.6px; line-height: 14.8px;
  }
  .publisher-about h3 { font-weight: 400; font-size: 11px; text-align: center; }
  .publisher-about p { text-align: justify; }

  /* ---------- Spine ---------- */
  .spine-title {
    position: absolute; left: 595px; top: 75px;
    transform-origin: 0 0; transform: rotate(90deg);
    white-space: nowrap; display: flex; align-items: baseline;
    height: 0;
  }
  .spine-title .script { font-family: "Allura", cursive; color: var(--white); font-size: 52px; line-height: 0; }
  .spine-title .caps {
    font-family: "Cinzel", serif; font-weight: 700; color: var(--navy);
    font-size: 30px; line-height: 0; margin: 0 8px; letter-spacing: 1px;
    text-shadow: 1px 1px 0 var(--white);
  }
  .spine-publisher {
    position: absolute; left: 592px; top: 650px;
    transform-origin: 0 0; transform: rotate(90deg);
    white-space: nowrap; color: var(--white); font-size: 9px; line-height: 12px;
  }
  .spine-mark {
    position: absolute; left: 597px; top: 711px; width: 22px; height: 22px;
    border-radius: 50%; background: var(--white);
  }

  /* ---------- Front cover ---------- */
  .front-title { position: absolute; left: 646px; top: 0; width: 554px; height: 300px; }
  .front-title .the {
    position: absolute; left: 110px; top: 30px;
    font-family: "Allura", cursive; color: var(--white); font-size: 110px; line-height: 1;
  }
  .front-title .quiet {
    position: absolute; left: 0; width: 554px; top: 112px; text-align: center;
    font-family: "Cinzel", serif; font-weight: 700; color: var(--navy);
    font-size: 52px; letter-spacing: 2px; line-height: 1;
    text-shadow: 2px 2px 0 var(--white);
  }
  .front-title .harvest {
    position: absolute; right: 8px; top: 150px;
    font-family: "Allura", cursive; color: var(--white); font-size: 118px; line-height: 1;
  }
  .butterfly-art {
    position: absolute; left: 736px; top: 325px; width: 372px; height: 278px;
    border-radius: 48% 48% 40% 40% / 40% 40% 55% 55%;
    background: radial-gradient(ellipse at 50% 70%, var(--wing-light) 0%, var(--wing-mid) 45%, var(--wing-deep) 85%);
    box-shadow: 4px 6px 8px rgba(0,0,0,0.35);
  }
  .front-subtitle {
    position: absolute; left: 646px; width: 554px; top: 672px;
    text-align: center; color: var(--white);
    font-family: "Old Standard TT", serif; font-size: 16px; line-height: 17px;
    letter-spacing: 1.6px;
  }
  .front-publisher {
    position: absolute; left: 646px; width: 554px; top: 754px;
    display: flex; flex-direction: column; align-items: center;
  }
  .front-publisher .mark { width: 30px; height: 30px; border-radius: 50%; background: var(--navy); }
  .front-publisher .name { margin-top: 2px; color: var(--navy); font-size: 15px; letter-spacing: -0.2px; }
</style>
</head>
<body>
<main class="cover-wrap">

  <!-- Back cover -->
  <header class="back-title">
    <h2>THE QUIET HARVEST</h2>
    <p>LESSONS OF INSIGHT FROM A CIRCLE OF MENTORS<br>TO GUIDE YOU TOWARD A FULLER JOURNEY</p>
  </header>

  <section class="blurb">
    <p>A coach does not fix you. Or heal you. They coach you - by offering thoughts to ponder, guidance, techniques to try - All to help you play and succeed at the game of life.</p>
    <p>Each coach has their own personality, training, experience, method and philosophy they bring to the table. The underlying purpose is to guide you through the quiet harvest, to become the person you desire and aspire to be. Different coaches for different folks, yet they all have their own unique wisdom and special sauce to share.</p>
    <p>This book is a collection of just that. A tasting of the wisdom and philosophies of a variety of different coaches for you to experience.</p>
  </section>

  <h3 class="authors-heading">Authors names</h3>
  <ul class="author-list col-a">
    <li>Author name</li><li>Author name</li><li>Author name</li><li>Author name</li><li>Author name</li>
    <li>Author name</li><li>Author name</li><li>Author name</li><li>Author name</li><li>Author name</li>
  </ul>
  <ul class="author-list col-b">
    <li>Author name</li><li>Author name</li><li>Author name</li><li>Author name</li><li>Author name</li>
    <li>Author name</li><li>Author name</li><li>Author name</li><li>Author name</li><li>Author name</li>
  </ul>

  <div class="publisher-band"></div>
  <section class="publisher-about">
    <h3>About the Publisher</h3>
    <p>The Lantern Publishing House is the publishing arm of The Lantern to Wellness, a company founded and led by Dr. Marisol Voyle DPT in order to engage, educate, inspire, and empower healing and love within yourself and for others. The Lantern Publishing House seeks to unlock the true potential of each individual to amplify their voice and message and to improve our human experience. Please visit https://thelanterntowellness.net to learn about future publications.</p>
  </section>

  <!-- Spine -->
  <div class="spine-title">
    <span class="script">the</span><span class="caps">QUIET</span><span class="script">harvest</span>
  </div>
  <div class="spine-publisher">THE LANTERN PUBLISHING HOUSE</div>
  <div class="spine-mark"></div>

  <!-- Front cover -->
  <h1 class="front-title">
    <span class="the">the</span>
    <span class="quiet">QUIET</span>
    <span class="harvest">harvest</span>
  </h1>

  <div class="butterfly-art" role="img" aria-label="Illustration of a deep blue butterfly with turquoise-tipped wings, viewed from above"></div>

  <p class="front-subtitle">LESSONS OF INSIGHT FROM A CIRCLE<br>OF MENTORS TO GUIDE YOU TOWARD<br>A FULLER JOURNEY</p>

  <div class="front-publisher">
    <span class="mark"></span>
    <span class="name">The Lantern Publishing House</span>
  </div>

</main>
</body>
</html>
```